Interior Stylist business card design needed

I need a business card for my new company in Sydney called "Liv Harrowby Designs". The business offers an interior styling and colour consultancy. My clients are generally not very design savvy (hence why they use me) and can range from being quite conservative to really wanting something "out there". They can be looking for a budget makeover or something more expensive / substantial. I'd like my business card design to be stylish (but not overly formal). I certainly don't want it to be conservative. I'd like it to stand out a bit! I don't really have any aversion to particular colours and I don't have a logo as such - my business name is really all I have.

Target Market(s)

As above - home owners, ranging from conservative to modern

Industry/Entity Type

Conservative

Contact Information for Business Card

Liv Harrowby Designs
Colour consultancy and interior styling
ph: 0417 238 605
email: livharrowby@qoralnet.net.au

Requirements
Should not have
• Old fashioned writing or motifs. No Times Roman font!!

```html
<!DOCTYPE html>
<html lang="en">
<head>
<meta charset="utf-8">
<title>Liv Harrowby Designs – Business Card</title>
<link href="https://fonts.googleapis.com/css2?family=Open+Sans:wght@400;700&display=swap" rel="stylesheet">
<style>
  :root {
    --backdrop: #d8d8d8;
    --card: #050505;
    --ink: #ffffff;
    --sun: #ecd046;
    --flame: #ee6d3f;
    --cyan: #4cc2e8;
    --periwinkle: #7a8ac6;
  }
  * { margin: 0; padding: 0; box-sizing: border-box; }
  html, body {
    width: 1200px;
    height: 741px;
    overflow: hidden;
    background: var(--backdrop);
    font-family: "Open Sans", Arial, sans-serif;
  }
  .canvas {
    width: 1200px;
    height: 741px;
    display: flex;
    align-items: center;
    justify-content: center;
  }
  .business-card {
    position: relative;
    width: 880px;
    height: 510px;
    background: var(--card);
    overflow: hidden;
    box-shadow: 0 6px 18px rgba(0,0,0,0.18);
  }
  .paint-swatch {
    position: absolute;
    left: 470px;
    right: 0;
    top: 30px;
    height: 390px;
    background: linear-gradient(180deg,
      var(--sun) 0%, var(--flame) 40%, var(--cyan) 72%, var(--periwinkle) 100%);
  }
  .identity {
    position: absolute;
    left: 60px;
    top: 228px;
    width: 390px;
    color: var(--ink);
    text-align: center;
  }
  .identity__name {
    font-weight: 700;
    font-size: 32px;
    line-height: 1.15;
    white-space: nowrap;
  }
  .identity__tagline {
    font-size: 14px;
    text-align: right;
    white-space: nowrap;
    margin-top: 2px;
  }
  .contact {
    list-style: none;
    margin-top: 36px;
    font-size: 21px;
    line-height: 1;
  }
  .contact li + li { margin-top: 30px; }
</style>
</head>
<body>
  <main class="canvas">
    <article class="business-card">
      <div class="paint-swatch" role="img" aria-label="Painted brushstroke colour swatches in yellow, orange and blue tones"></div>
      <section class="identity">
        <h1 class="identity__name">Liv Harrowby Designs</h1>
        <p class="identity__tagline">Colour Consultancy &amp; Interior Styling</p>
        <ul class="contact">
          <li class="contact__phone">0417 238 605</li>
          <li class="contact__email">livharrowby@qoralnet.net.au</li>
        </ul>
      </section>
    </article>
  </main>
</body>
</html>
```